KVOR Individual and Corporate Development Business Card Design

KVOR needs a business card design that is aligned with it's values and targetted markets. Coherent Lattice of Adaptive Reasoning Method's self diagnosis model and tools, which can be used for personal improvement and team/business performance enhancement, is based on the learnings of over 20 years of medical practitioning. KVOR supercharges personal effectiveness and awareness to also increase team and business performance.

The targetted markets are high performance individuals and teams who aspire seek to enhance their capabilities and achieve their absolute best potential.

Look and feel for the business card design we are looking for is high technology, premium, fresh, new and medical.

Target Market(s)

Industry/Entity Type

Business Consultant

Contact Information for Business Card

Logo, Full Name, Title, Phone number, Email, company name, Address,

Font styles to use
Sans Serif

Requirements
Must have
• Tag line: Maximising Performance for Highly Effective People
• Please use same colours as the logo.

```html
<!DOCTYPE html>
<html lang="en">
<head>
<meta charset="utf-8">
<title>KVOR Business Card</title>
<link rel="stylesheet" href="https://fonts.googleapis.com/css2?family=Source+Sans+3:wght@400;600;700&display=swap">
<style>
  :root {
    --backdrop: #141414;
    --card-white: #ffffff;
    --brand-blue: #29abe2;
    --brand-teal: #1ba6b8;
    --ink: #1a1a1a;
    --on-blue: #ffffff;
  }
  * { margin: 0; padding: 0; box-sizing: border-box; }
  html, body {
    width: 1200px; height: 900px; overflow: hidden;
    background: var(--backdrop);
    font-family: "Source Sans 3", Arial, sans-serif;
  }
  .stage { position: relative; width: 1200px; height: 900px; }
  .card {
    position: absolute; top: 170px;
    width: 347px; height: 561px;
    overflow: hidden;
  }
  .card-front { left: 259px; background: var(--card-white); text-align: center; }
  .card-back { left: 631px; background: var(--brand-blue); }

  .holder-name {
    position: absolute; top: 58px; left: 0; right: 0;
    color: var(--brand-blue); font-weight: 700; font-size: 23px; letter-spacing: 0.2px;
  }
  .holder-title {
    position: absolute; top: 85px; left: 0; right: 0;
    color: var(--ink); font-size: 15px; text-transform: uppercase;
  }
  .contact-list {
    position: absolute; top: 150px; left: 0; right: 0;
    color: var(--ink); font-size: 15px; line-height: 19px; list-style: none;
  }
  .address {
    position: absolute; top: 243px; left: 0; right: 0;
    color: var(--ink); font-size: 15.5px; line-height: 20px; font-style: normal;
  }
  .company-mark {
    position: absolute; top: 328px; left: 0; right: 0;
    color: var(--brand-teal); font-weight: 700;
  }
  .company-mark .mark-name { display: block; font-size: 50px; line-height: 54px; letter-spacing: 3px; }
  .company-mark .mark-full { display: block; font-size: 13px; line-height: 16px; text-transform: uppercase; margin-top: 4px; }
  .tagline-band {
    position: absolute; left: 0; right: 0; bottom: 0; height: 99px;
    background: var(--brand-blue); color: var(--on-blue);
    font-weight: 700; font-size: 15.5px; line-height: 20px;
    display: flex; align-items: center; justify-content: center;
    text-transform: uppercase;
  }

  .back-mark {
    position: absolute; left: 50%; top: 50%;
    width: 320px;
    transform: translate(-50%, -50%) rotate(-90deg);
    color: var(--on-blue); display: flex; align-items: center; gap: 14px;
  }
  .back-mark .mark-name { font-weight: 700; font-size: 62px; letter-spacing: 4px; line-height: 1; }
  .back-mark .mark-rule { width: 1px; align-self: stretch; background: rgba(255,255,255,0.6); }
  .back-mark .mark-full { font-size: 17px; line-height: 20px; text-transform: uppercase; letter-spacing: 0.5px; }
</style>
</head>
<body>
<main class="stage">
  <section class="card card-front">
    <h1 class="holder-name">MARCUS DELANEY</h1>
    <p class="holder-title">Managing Director</p>
    <ul class="contact-list">
      <li>888 555 777</li>
      <li>INFO@KVOR.COM</li>
      <li>WWW.KVOR.COM</li>
    </ul>
    <address class="address">ADDRESS LINE ONE HERE,<br>ADDRESS LINE TWO HERE.</address>
    <div class="company-mark">
      <span class="mark-name">KVOR</span>
      <span class="mark-full">Coherent Lattice of<br>Adaptive Reasoning Method</span>
    </div>
    <p class="tagline-band">Maximising Performance<br>for<br>Highly Effective People</p>
  </section>

  <section class="card card-back">
    <div class="back-mark">
      <span class="mark-name">KVOR</span>
      <span class="mark-rule"></span>
      <span class="mark-full">Coherent Lattice of<br>Adaptive Reasoning Method</span>
    </div>
  </section>
</main>
</body>
</html>
```